BLS Business Card 2018

Larkmere Chiropractic. We have two locations that we want to advertise on the same card. Brightvale OrthoCore campus address: 3815 Pellham Dr., Suite 240, Flowood, MS 39417. Madison address: 246 Willowmere Dr., Building D., Madison, MS 39284. website: www.drlarkmere-example.com. o:(601)555-0147 f:(601)555-0183

Target Market(s)

Health care decision makers: primary care doctors and mothers

Contact Information for Business Card

I have no idea; up for any suggestions and I'd do much better picking from examples versus describing what I'm looking for. We are in a very high end location and would like the cards to look really sharp.

Requirements
Must have
• My name, Martin R Belvane, D.C.

```html
<!DOCTYPE html>
<html lang="en">
<head>
<meta charset="utf-8">
<title>Larkmere Chiropractic – Business Card</title>
<link rel="stylesheet" href="https://fonts.googleapis.com/css2?family=Cinzel:wght@400;600&family=Open+Sans:wght@400;600&display=swap">
<style>
  :root {
    --backdrop: #1a1a1a;
    --card: #1e1e1f;
    --card-edge: #2a2a2b;
    --ink: #f2f2f2;
    --ink-soft: #cfcfcf;
    --rule: #4a4a4a;
  }
  * { box-sizing: border-box; margin: 0; padding: 0; }
  html, body { width: 1200px; height: 900px; overflow: hidden; }
  body {
    background: var(--backdrop);
    font-family: "Open Sans", Arial, sans-serif;
    color: var(--ink);
    position: relative;
  }
  .card {
    position: absolute;
    width: 560px;
    height: 320px;
    background: var(--card);
    border: 1px solid var(--card-edge);
    border-radius: 22px;
    box-shadow: 0 18px 40px rgba(0,0,0,0.55);
  }
  .card--back { left: 90px; top: 90px; }
  .card--front { left: 550px; top: 490px; }

  .brand {
    position: absolute;
    display: flex;
    align-items: center;
    gap: 14px;
  }
  .brand__mark {
    width: 34px; height: 34px;
    border: 1.5px solid var(--ink);
    border-radius: 50%;
  }
  .brand__name {
    font-family: "Cinzel", Georgia, serif;
    font-weight: 600;
    color: var(--ink);
    line-height: 1;
  }
  .brand__name span { display: block; }
  .brand__name .line-1 { font-size: 34px; letter-spacing: 1px; }
  .brand__name .line-2 { font-size: 23px; letter-spacing: 1.5px; margin-top: 2px; }

  .rule {
    position: absolute;
    height: 1px;
    background: var(--rule);
  }

  /* back */
  .card--back .brand { left: 150px; top: 92px; }
  .card--back .rule--top { left: 230px; right: 40px; top: 170px; }
  .card--back .rule--bottom { left: 40px; right: 150px; top: 250px; }
  .location {
    position: absolute;
    right: 50px;
    top: 188px;
    text-align: right;
    font-size: 14px;
    line-height: 1.45;
  }
  .location__name { font-weight: 600; color: var(--ink); }
  .location__address { color: var(--ink-soft); }

  /* front */
  .card--front .brand { left: 250px; top: 28px; }
  .card--front .rule--top { left: 380px; right: 40px; top: 104px; }
  .campus {
    position: absolute;
    right: 40px;
    top: 114px;
    text-align: right;
    font-size: 14px;
    line-height: 1.4;
    color: var(--ink-soft);
  }
  .campus__name { color: var(--ink); }
  .card--front .rule--mid { left: 40px; right: 230px; top: 204px; }
  .person {
    position: absolute;
    left: 40px;
    top: 212px;
    font-family: "Cinzel", Georgia, serif;
    font-weight: 600;
    font-size: 21px;
    letter-spacing: 1px;
    white-space: nowrap;
  }
  .contact {
    position: absolute;
    left: 40px;
    top: 250px;
    list-style: none;
    font-size: 14px;
    line-height: 1.4;
    color: var(--ink-soft);
  }
  .contact li { display: flex; align-items: center; gap: 8px; }
  .contact svg { width: 13px; height: 13px; fill: var(--ink); flex: none; }
</style>
</head>
<body>

  <section class="card card--back" aria-label="Business card, back">
    <div class="brand">
      <div class="brand__mark"></div>
      <div class="brand__name"><span class="line-1">LARKMERE</span><span class="line-2">CHIROPRACTIC</span></div>
    </div>
    <div class="rule rule--top"></div>
    <div class="location">
      <div class="location__name">MADISON</div>
      <div class="location__address">246 Willowmere Dr., Building D., Madison, MS 39284.</div>
    </div>
    <div class="rule rule--bottom"></div>
  </section>

  <section class="card card--front" aria-label="Business card, front">
    <div class="brand">
      <div class="brand__mark"></div>
      <div class="brand__name"><span class="line-1">LARKMERE</span><span class="line-2">CHIROPRACTIC</span></div>
    </div>
    <div class="rule rule--top"></div>
    <div class="campus">
      <div class="campus__name">BRIGHTVALE ORTHOCORE<br>CAMPUS</div>
      <div>3815 Pellham Dr., Suite 240</div>
      <div>Flowood, MS 39417</div>
    </div>
    <div class="rule rule--mid"></div>
    <div class="person">MARTIN R BELVANE, D.C.</div>
    <ul class="contact">
      <li>
        <svg viewBox="0 0 16 16" aria-hidden="true"><path d="M2 6c0-2 2-3 6-3s6 1 6 3l-3 1-1-2H6L5 7 2 6zm2 2h8l1 5H3l1-5zm4 1.5a1.5 1.5 0 100 3 1.5 1.5 0 000-3z"/></svg>
        (601)555-0147
      </li>
      <li>
        <svg viewBox="0 0 16 16" aria-hidden="true"><path d="M4 1h8v4H4zM2 6h12v6h-2v3H4v-3H2zm3 5v3h6v-3z"/></svg>
        (601)555-0183
      </li>
      <li>
        <svg viewBox="0 0 16 16" aria-hidden="true"><path d="M8 1a7 7 0 100 14A7 7 0 008 1zm0 1.5c.8 0 1.7 1.6 2 4H6c.3-2.4 1.2-4 2-4zM6 8h4c0 2.8-1 5.5-2 5.5S6 10.8 6 8zm-3.4-1.5h2C4.7 4.8 5 3.6 5.5 3A5.5 5.5 0 002.6 6.5zm8.8 0h2A5.5 5.5 0 0010.5 3c.5.6.8 1.8.9 3.5zM2.6 8h2c0 1.9.4 3.6 1 5a5.5 5.5 0 01-3-5zm8.8 0h2a5.5 5.5 0 01-3 5c.6-1.4 1-3.1 1-5z"/></svg>
        www.drlarkmere-example.com
      </li>
    </ul>
  </section>

</body>
</html>
```